Business Card Design For A Cajun Seafood Restaurant

We are opening a cajun seafood restaurant in a week. We mainly serve cajun seafood which is orginally from Louisiana. We want design on both sides of a business card. I have menu on the website. You can go to www.reednkettle.example to check out our menu.

Restaurant name: Reed N' Kettle
Phone: +1 (555) 304-7712
Address: 48206 Ludlow Row, #7, Bexmoor Flats, Ca90000
Email: reednkettle@mailbox.example
Website: www.reednkettle.example

Maybe add social media icons (facebook, instagram) if looks nice on the business card.
facebook.com/reednkettle
instagram.com/reednkettle or @reednkettle

Attached is the logo and other business card samples that I like.

```html
<!DOCTYPE html>
<html lang="en">
<head>
<meta charset="utf-8">
<title>Reed N' Kettle — Business Card</title>
<link href="https://fonts.googleapis.com/css2?family=Source+Sans+3:wght@400;600&display=swap" rel="stylesheet">
<style>
  :root {
    --backdrop: #3a3a3a;
    --card-white: #f7f7f7;
    --ink: #000000;
    --text-light: #ffffff;
    --orange: #f55f00;
    --name-orange: #f47a20;
    --gold: #f5b800;
    --crab-red: #e2541a;
    --corn-yellow: #f2c51c;
  }
  * { box-sizing: border-box; margin: 0; padding: 0; }
  html, body { width: 1200px; height: 750px; overflow: hidden; }
  body {
    background: var(--backdrop);
    font-family: "Source Sans 3", "Myriad Pro", sans-serif;
    position: relative;
  }
  .card {
    position: absolute;
    top: 228px;
    width: 461px;
    height: 262px;
    border-radius: 16px;
    overflow: hidden;
  }
  .card--front { left: 124px; background: var(--card-white); }
  .card--back { left: 618px; background: var(--orange); }

  .front-wave { position: absolute; inset: 0; width: 100%; height: 100%; }

  .mascot {
    position: absolute;
    border-radius: 50%;
    background: radial-gradient(circle at 50% 40%, var(--corn-yellow) 0%, var(--crab-red) 55%, rgba(226,84,26,0.85) 100%);
  }
  .mascot--small { left: 76px; top: 24px; width: 80px; height: 70px; }
  .mascot--large {
    left: 146px; top: 48px; width: 172px; height: 168px;
    background: radial-gradient(circle at 50% 35%, var(--corn-yellow) 0%, #e8481a 50%, #d94512 100%);
  }

  .brand-name {
    position: absolute;
    left: 26px; top: 98px; width: 172px;
    text-align: center;
    font-size: 20px; font-weight: 600;
    color: var(--ink);
    letter-spacing: 0.3px;
    white-space: nowrap;
  }

  .contact {
    position: absolute;
    right: 28px; top: 102px;
    text-align: right;
    color: var(--text-light);
    white-space: nowrap;
  }
  .contact__name { font-size: 17px; font-weight: 600; color: var(--name-orange); line-height: 19px; }
  .contact__title { font-size: 13.5px; color: var(--gold); line-height: 17px; margin-bottom: 8px; }
  .contact__address { font-size: 12.5px; line-height: 17px; margin-bottom: 7px; }
  .contact__line {
    display: flex; justify-content: flex-end; align-items: center; gap: 6px;
    font-size: 12.5px; line-height: 17.5px;
  }
  .contact__line svg { width: 11px; height: 11px; flex: none; }

  .social {
    position: absolute;
    left: 0; right: 0; top: 220px;
    display: flex; justify-content: center; align-items: center; gap: 4px;
    color: var(--text-light); font-size: 13px;
  }
  .social__item { display: flex; align-items: center; gap: 4px; }
  .social__dot { width: 17px; height: 17px; border-radius: 50%; background: var(--text-light); }
</style>
</head>
<body>

<section class="card card--front">
  <svg class="front-wave" viewBox="0 0 461 262" preserveAspectRatio="none" aria-hidden="true">
    <path d="M0,184 C50,222 110,226 160,206 C200,190 230,150 262,116 C310,66 370,48 461,48 L461,262 L0,262 Z" fill="var(--ink)"/>
    <path d="M140,222 C190,215 215,170 250,126 C300,66 360,36 436,38" fill="none" stroke="var(--orange)" stroke-width="5"/>
    <path d="M8,186 C40,215 90,214 120,210 C160,204 185,185 200,162" fill="none" stroke="var(--gold)" stroke-width="5"/>
  </svg>

  <div class="mascot mascot--small" role="img" aria-label="Cartoon crab mascot holding an ear of corn"></div>
  <div class="brand-name">Reed N' Kettle</div>

  <div class="contact">
    <div class="contact__name">DALE THIBODEAUX</div>
    <div class="contact__title">CEO/Founder</div>
    <div class="contact__address">48206 Ludlow Row, #7<br>Bexmoor Flats, Ca90000</div>
    <div class="contact__line">+1 (555) 304-7712
      <svg viewBox="0 0 24 24"><path fill="var(--name-orange)" d="M6.6 10.8a15 15 0 0 0 6.6 6.6l2.2-2.2a1 1 0 0 1 1-.25 11.4 11.4 0 0 0 3.6.57 1 1 0 0 1 1 1V20a1 1 0 0 1-1 1A17 17 0 0 1 3 4a1 1 0 0 1 1-1h3.5a1 1 0 0 1 1 1c0 1.25.2 2.45.57 3.57a1 1 0 0 1-.25 1z"/></svg>
    </div>
    <div class="contact__line">reednkettle@mailbox.example
      <svg viewBox="0 0 24 24"><rect x="2" y="5" width="20" height="14" fill="var(--name-orange)"/><path d="M2 5l10 8 10-8" fill="none" stroke="var(--ink)" stroke-width="1.6"/></svg>
    </div>
    <div class="contact__line">www.reednkettle.example
      <svg viewBox="0 0 24 24"><circle cx="12" cy="12" r="10" fill="var(--name-orange)"/><path d="M2 12h20M12 2c3 3 3 17 0 20M12 2c-3 3-3 17 0 20" fill="none" stroke="var(--ink)" stroke-width="1.4"/></svg>
    </div>
  </div>
</section>

<section class="card card--back">
  <div class="mascot mascot--large" role="img" aria-label="Large cartoon crab mascot holding an ear of corn"></div>
  <div class="social">
    <span class="social__item"><span class="social__dot"></span>reednkettle</span>
    <span class="social__item"><span class="social__dot"></span>@reednkettle</span>
  </div>
</section>

</body>
</html>
```